Oil and Gas Exploration and Production company needs a business card design

We need a business card design using our logo and colors in the logo. We want a mainstream design.

```html
<!DOCTYPE html>
<html lang="en">
<head>
<meta charset="utf-8">
<title>Sola Oil &amp; Gas – Business Card</title>
<link href="https://fonts.googleapis.com/css2?family=Zilla+Slab:wght@700&family=Open+Sans:wght@400&display=swap" rel="stylesheet">
<style>
  :root {
    --backdrop: #f1ece0;
    --card-white: #ffffff;
    --gold-deep: #c3902c;
    --gold: #d3a33d;
    --gold-soft: #dcb352;
    --sand: #efe6d6;
    --cream: #fbf3df;
    --ink: #1d1b18;
  }
  * { margin: 0; padding: 0; box-sizing: border-box; }
  html, body {
    width: 1200px; height: 873px; overflow: hidden;
    background: var(--backdrop);
  }
  .stage {
    width: 1200px; height: 873px;
    display: flex; align-items: center; justify-content: center;
  }
  .business-card {
    position: relative;
    width: 840px; height: 480px;
    background: var(--card-white);
    overflow: hidden;
    box-shadow: 0 18px 40px rgba(90, 70, 30, 0.18);
  }
  .card-art { position: absolute; inset: 0; }
  .brand {
    position: absolute; left: 56px; top: 168px;
    display: flex; align-items: center; gap: 14px;
    font-family: "Zilla Slab", Georgia, serif;
    font-weight: 700; color: var(--ink);
  }
  .brand-dot {
    width: 30px; height: 30px; border-radius: 50%;
    background: var(--ink); flex: none;
  }
  .brand-name { line-height: 0.95; }
  .brand-name .main { display: block; font-size: 92px; }
  .brand-name .sub { display: block; font-size: 30px; letter-spacing: 0.18em; margin-top: 6px; }
  .website {
    position: absolute; left: 58px; bottom: 28px;
    font-family: "Open Sans", Arial, sans-serif;
    font-size: 23px; color: var(--gold-deep);
  }
  .contact-block {
    position: absolute; left: 520px; top: 212px;
    font-family: "Open Sans", Arial, sans-serif; color: var(--ink);
  }
  .person-name {
    font-family: "Zilla Slab", Georgia, serif; font-weight: 700;
    font-size: 34px; color: var(--cream); line-height: 1;
  }
  .person-role {
    font-size: 15px; letter-spacing: 0.6em; color: var(--cream);
    margin: 8px 0 26px;
  }
  .contact-list { list-style: none; }
  .contact-list li {
    display: flex; align-items: center; gap: 10px;
    font-size: 20px; line-height: 1.7;
  }
  .contact-list svg { width: 16px; height: 16px; flex: none; fill: var(--ink); }
</style>
</head>
<body>
<main class="stage">
  <article class="business-card">
    <svg class="card-art" viewBox="0 0 840 480" width="840" height="480">
      <g role="img" aria-label="Faint sun-drop decorations">
        <circle cx="420" cy="20" r="95" fill="var(--sand)"/>
        <circle cx="330" cy="150" r="62" fill="var(--sand)"/>
        <circle cx="470" cy="135" r="30" fill="var(--sand)"/>
      </g>
      <path class="panel-back" d="M430 480 V250 Q430 140 540 140 H840 V480 Z" fill="var(--gold-deep)"/>
      <path class="panel-front" d="M470 480 V230 Q470 185 515 185 H840 V480 Z" fill="var(--gold)"/>
      <circle role="img" aria-label="Large faint sun emblem" cx="700" cy="390" r="150" fill="var(--gold-soft)" opacity="0.55"/>
    </svg>

    <div class="brand">
      <span class="brand-dot"></span>
      <span class="brand-name"><span class="main">Sola</span><span class="sub">OIL &amp; GAS</span></span>
    </div>

    <p class="website">www.sola-oilandgas.com</p>

    <section class="contact-block">
      <h1 class="person-name">Your Name</h1>
      <p class="person-role">OWNER</p>
      <ul class="contact-list">
        <li><svg viewBox="0 0 16 16"><path d="M3.5 1l2.5 3-1.5 2c1 2 3 4 5 5l2-1.5 3 2.5-1.5 2.5C8 15 1 8 1 2.5z"/></svg>(262) 000-0000</li>
        <li><svg viewBox="0 0 16 16"><path d="M1 3h14v10H1zm1.5 1.5v.4L8 9l5.5-4.1v-.4zm0 2.3v4.7h11V6.8L8 10.9z"/></svg>sola@sola-oilandgas.com</li>
        <li><svg viewBox="0 0 16 16"><path d="M8 0a5.5 5.5 0 0 0-5.5 5.5C2.5 10 8 16 8 16s5.5-6 5.5-10.5A5.5 5.5 0 0 0 8 0zm0 8a2.5 2.5 0 1 1 0-5 2.5 2.5 0 0 1 0 5z"/></svg>your office address</li>
      </ul>
    </section>
  </article>
</main>
</body>
</html>
```